Business Card front and back

I am looking for business card design. I really really like the design file I uploaded named 627788_19250069_3478263_85f427ee_image

Target Market(s)

Corporate Fitness High end Private country club

Industry/Entity Type

Fitness Industry

Contact Information for Business Card

The last image I like as an example I uploaded a bunch of my logos. The file labeled "the signature" is my business card information for you to use

Colors
0054AA
0677BA
7BADD7
CADEEF
E8F1F8

Requirements
Must have
• E-mail sigThe file I uploaded labeled "627788_19250069_3478263_85f427ee_image" with all the plus signs on the back if those could be the logo symbol I uploaded labeled "1 back.png"

```html
<!DOCTYPE html>
<html lang="en">
<head>
<meta charset="utf-8">
<title>Stride Works – Business Card</title>
<link rel="stylesheet" href="https://fonts.googleapis.com/css2?family=Open+Sans:wght@400;600;700&family=Saira:wght@700;800&display=swap">
<style>
  :root {
    --page: #e9ecef;
    --ink: #2b2d30;
    --charcoal: #2f3033;
    --charcoal-deep: #141516;
    --charcoal-light: #5a5c60;
    --brand-blue: #3f7cc4;
    --paper: #ffffff;
    --photo-light: #8a8d90;
    --photo-dark: #2a2b2d;
    --ring: #ddd3d6;
  }
  * { box-sizing: border-box; margin: 0; padding: 0; }
  html, body { width: 1200px; height: 900px; overflow: hidden; }
  body {
    background: var(--page);
    font-family: "Open Sans", Arial, sans-serif;
    color: var(--ink);
    position: relative;
  }
  .card {
    position: absolute;
    width: 700px;
    height: 400px;
    left: 250px;
    overflow: hidden;
    box-shadow: 0 8px 24px rgba(0,0,0,0.18);
  }

  /* Back */
  .card-back { top: 35px; background: var(--charcoal); }
  .back-pattern {
    position: absolute; inset: 0;
    background:
      radial-gradient(ellipse at 85% 10%, rgba(255,255,255,0.12) 0%, rgba(255,255,255,0) 55%),
      linear-gradient(to top right, var(--charcoal-deep) 0%, var(--charcoal) 55%, var(--charcoal-light) 100%);
  }
  .back-brand {
    position: absolute;
    left: 50%; top: 50%;
    transform: translate(-50%, -50%);
    display: flex; align-items: center; gap: 10px;
    font-weight: 700; font-size: 22px; letter-spacing: 2px;
    color: var(--paper);
    white-space: nowrap;
  }
  .mark-square { display: block; background: var(--brand-blue); flex: none; }
  .back-brand .mark-square { width: 18px; height: 18px; }

  /* Front */
  .card-front { top: 465px; background: var(--paper); }
  .front-brand {
    position: absolute; left: 62px; top: 48px;
    display: flex; flex-direction: column; align-items: center; gap: 10px;
    font-weight: 700; font-size: 26px; letter-spacing: 2px;
    color: var(--ink);
    white-space: nowrap;
  }
  .front-brand .mark-square { width: 40px; height: 40px; }
  .person { position: absolute; left: 62px; top: 140px; }
  .person-name {
    font-family: "Saira", "Arial Black", sans-serif;
    font-weight: 800; font-size: 32px; line-height: 1; letter-spacing: 1px;
    color: var(--ink);
  }
  .person-name .surname { color: var(--brand-blue); }
  .person-role { font-size: 17px; margin-top: 4px; letter-spacing: 0.5px; }
  .contact-list { list-style: none; margin-top: 14px; }
  .contact-list li {
    display: flex; align-items: center; gap: 12px;
    font-size: 17px; line-height: 1.55; letter-spacing: 0.3px;
  }
  .contact-list svg { width: 18px; height: 18px; flex: none; }
  .portrait {
    position: absolute; left: 450px; top: 28px;
    width: 205px; height: 205px; border-radius: 50%;
    border: 4px solid var(--ring);
    background: radial-gradient(circle at 45% 40%, var(--photo-light) 0%, var(--photo-dark) 75%);
  }
  .swoosh { position: absolute; inset: 0; width: 700px; height: 400px; }
  .region {
    position: absolute; right: 40px; bottom: 40px;
    display: flex; align-items: center; gap: 8px;
    color: var(--paper); font-size: 15px; letter-spacing: 0.5px;
  }
  .region svg { width: 14px; height: 18px; }
</style>
</head>
<body>

<section class="card card-back" aria-label="Card back">
  <div class="back-pattern" role="img" aria-label="Repeating embossed brand symbol pattern on charcoal, darker at lower left and lighter at upper right"></div>
  <div class="back-brand"><span class="mark-square"></span>STRIDE WORKS</div>
</section>

<section class="card card-front" aria-label="Card front">
  <svg class="swoosh" viewBox="0 0 700 400" aria-hidden="true">
    <path d="M0,312 C200,330 400,295 560,232 C420,305 220,345 0,336 Z" fill="var(--brand-blue)"/>
    <path d="M0,346 C260,362 480,300 700,190 L700,400 L0,400 Z" fill="var(--charcoal)"/>
  </svg>

  <div class="front-brand"><span class="mark-square"></span>STRIDE WORKS</div>

  <div class="person">
    <h1 class="person-name">DANA <span class="surname">MORRELL</span></h1>
    <p class="person-role">Consultant</p>
    <ul class="contact-list">
      <li>
        <svg viewBox="0 0 24 24"><path d="M6.6 10.8a15 15 0 0 0 6.6 6.6l2.2-2.2a1 1 0 0 1 1-.25 11.4 11.4 0 0 0 3.6.57 1 1 0 0 1 1 1V20a1 1 0 0 1-1 1A17 17 0 0 1 3 4a1 1 0 0 1 1-1h3.5a1 1 0 0 1 1 1c0 1.25.2 2.45.57 3.57a1 1 0 0 1-.25 1z" fill="var(--brand-blue)"/></svg>
        555-014-2737
      </li>
      <li>
        <svg viewBox="0 0 24 24"><rect x="2" y="5" width="20" height="14" rx="1" fill="var(--brand-blue)"/><path d="M2 6l10 7 10-7" stroke="#fff" stroke-width="1.6" fill="none"/></svg>
        dana@strideworks.co
      </li>
      <li>
        <svg viewBox="0 0 24 24" fill="none" stroke="var(--brand-blue)" stroke-width="1.8"><circle cx="12" cy="12" r="9.5"/><ellipse cx="12" cy="12" rx="4" ry="9.5"/><path d="M2.5 12h19M4 7h16M4 17h16"/></svg>
        www.strideworks.co
      </li>
    </ul>
  </div>

  <div class="portrait" role="img" aria-label="Portrait photo of the consultant"></div>

  <div class="region">
    <svg viewBox="0 0 14 18"><path d="M7 0a7 7 0 0 1 7 7c0 5-7 11-7 11S0 12 0 7a7 7 0 0 1 7-7z" fill="var(--brand-blue)"/><circle cx="7" cy="7" r="2.5" fill="var(--charcoal)"/></svg>
    OR.WA.ID.MT.WY
  </div>
</section>

</body>
</html>
```